Website for software company "velora"

We need a website for our software company/startup named "velora". We are developing several products (currently 3 standard-software products) which are all in different sectors, but all our products are available for Laptops/PC/Mobile Phones/Tablets, ... We do also create custom software and support our customers with consulting to optimize their processes.
We already have a Logo which you can find in the attached files.
We are a young team of 4 members (two founders and 2 employees).

To get an idea of our products -> the first one is a planning software for healthcare organizations (eg. BlueHaven, firebrigade, pharmacy), the second one is a booking software for sport clubs and the third one is a competition software for sports hunting. You see very diverse. Include or ignore this info of our products as you like.

The design has to be a bootstrap 4 (or higher) design. We have licenced FontAwesome as iconset. Responsive design should come without saying.

• Starting page, product pages, news section, contact, team, services

```html
<!DOCTYPE html>
<html lang="en">
<head>
<meta charset="utf-8">
<title>velora — Software for every sector</title>
<link rel="stylesheet" href="https://fonts.googleapis.com/css2?family=Montserrat:wght@300;400;500;600;700;800&family=Roboto:wght@400;500;700&display=swap">
<style>
:root{
  --orange:#ee6a25;
  --orange-dark:#d95a18;
  --navy:#1f2630;
  --navy-2:#252c36;
  --ink:#222;
  --text:#555;
  --grey:#d9d9d9;
  --peach:#f3dccd;
  --white:#fff;
  --social:#4a525c;
}
*{box-sizing:border-box;margin:0;padding:0}
html,body{width:1200px;height:4594px;overflow:hidden}
body{position:relative;background:var(--white);font-family:Roboto,Arial,sans-serif;color:var(--text)}
.abs{position:absolute}
h1,h2,h3{font-family:Montserrat,Arial,sans-serif}

/* header */
.site-header{position:absolute;left:0;top:0;width:1200px;height:104px;background:#fff;border-top:5px solid var(--orange);z-index:5}
.brand{position:absolute;left:110px;top:28px;font-family:Montserrat,sans-serif;font-weight:800;font-size:44px;letter-spacing:1px;color:var(--ink);line-height:1}
.main-nav{position:absolute;left:430px;top:45px;display:flex;gap:25px;font-family:Roboto,sans-serif;font-weight:700;font-size:13px;color:var(--ink)}
.main-nav .active{color:var(--orange);text-decoration:underline;text-underline-offset:5px}
.btn-login{position:absolute;left:988px;top:36px;width:100px;height:39px;background:var(--orange);color:#fff;font-weight:700;font-size:13px;display:flex;align-items:center;justify-content:center;gap:7px}

/* hero */
.hero{position:absolute;left:0;top:104px;width:1200px;height:782px;overflow:hidden}
.hero-photo{position:absolute;inset:0;background:linear-gradient(135deg,#6b737c 0%,#9aa2aa 35%,#c8ccd0 55%,#7b838a 80%,#4a5158 100%)}
.hero-shade{position:absolute;inset:0;background:rgba(20,25,30,.25)}
.hero-title{position:absolute;left:0;width:1200px;top:200px;text-align:center;font-family:Montserrat,sans-serif;font-weight:800;font-size:84px;color:#fff;letter-spacing:2px;line-height:1}
.hero-sub{position:absolute;left:0;width:1200px;top:306px;text-align:center;font-family:Montserrat,sans-serif;font-weight:700;font-size:25px;color:#fff}
.btn-orange{background:var(--orange);color:#fff;font-weight:700;font-size:13px;display:flex;align-items:center;justify-content:center;gap:8px;font-family:Roboto,sans-serif}
.hero-cta{position:absolute;left:524px;top:356px;width:152px;height:46px}
.hero-arrow{position:absolute;top:316px;width:46px;height:46px;border-radius:50%;background:rgba(255,255,255,.35);display:flex;align-items:center;justify-content:center}
.hero-edge{position:absolute;left:0;top:0}

/* about */
.eyebrow{position:absolute;font-family:Montserrat,sans-serif;font-size:20px;color:var(--orange);font-weight:500}
.section-title{position:absolute;font-family:Montserrat,sans-serif;font-weight:700;font-size:38px;color:var(--ink)}
.about-copy{position:absolute;left:110px;top:995px;width:478px;font-size:13.5px;line-height:26px;text-align:justify;color:#555}
.about-copy p+p{margin-top:26px}
.btn-learn{position:absolute;left:110px;top:1273px;width:150px;height:48px}
.photo{position:absolute}
.about-frame{position:absolute;left:713px;top:941px;width:294px;height:316px;border:5px solid var(--orange)}

/* software */
.software-title{position:absolute;left:0;width:1200px;top:1592px;text-align:center;font-family:Montserrat,sans-serif;font-weight:700;font-size:40px;color:#fff}
.software-title span,.accent{color:var(--orange)}
.hex-card{position:absolute;width:294px;height:322px}
.hex-card > .hex-shape{position:absolute;left:0;top:0}
.hex-icon{position:absolute;left:88px;top:64px;width:118px;height:118px;border-radius:50%;background:var(--peach);display:flex;align-items:center;justify-content:center}
.hex-label{position:absolute;left:0;width:294px;top:202px;text-align:center;font-family:Montserrat,sans-serif;font-weight:700;font-size:21px;line-height:26px;color:var(--ink)}

/* testimonials */
.center-title{position:absolute;left:0;width:1200px;text-align:center;font-family:Montserrat,sans-serif;font-size:40px;color:var(--ink)}
.center-title b{font-weight:700}
.center-title .light{font-weight:300}
.subtitle{position:absolute;left:0;width:1200px;text-align:center;font-size:18px;color:var(--orange)}
.avatar{position:absolute;border-radius:50%;background:linear-gradient(160deg,#cfd6dc,#8a96a3)}
.quote{position:absolute;left:215px;top:2622px;width:770px;text-align:center;font-size:13.5px;line-height:26px;color:#555}
.quote-author{position:absolute;left:0;width:1200px;top:2738px;text-align:center;font-size:18px;color:var(--orange)}
.dots{position:absolute;left:554px;top:2787px;display:flex;gap:7px}
.dots i{width:11px;height:11px;border-radius:50%;background:#d5d5d5;display:block}
.dots i.on{background:var(--orange)}
.dot-deco{position:absolute;border-radius:50%;background:var(--orange)}

/* news */
.news{position:absolute;left:0;top:2885px;width:1200px;height:615px;overflow:hidden;background:var(--orange)}
.news-photo{position:absolute;left:0;top:0;width:1200px;height:615px;background:linear-gradient(90deg,var(--orange) 0%,var(--orange) 42%,#c8773f 58%,#8d7f74 72%,#b4a89c 86%,#d6cbc0 100%)}
.news-title{position:absolute;left:110px;top:72px;font-family:Montserrat,sans-serif;font-size:40px;color:#fff}
.news-title .light{font-weight:300}
.news-title b{font-weight:700}
.news-arrow{position:absolute;top:86px}
.news-card{position:absolute;top:155px;width:315px;height:374px;background:#fff}
.news-img{position:absolute;left:14px;top:14px;width:287px;height:170px;background:linear-gradient(150deg,#b9c3cc,#6c7884)}
.news-date{position:absolute;left:25px;top:210px;font-size:13px;font-weight:500;color:var(--orange);display:flex;align-items:center;gap:5px}
.news-head{position:absolute;left:25px;top:243px;width:270px;font-family:Roboto,sans-serif;font-weight:700;font-size:19px;line-height:26px;color:var(--ink)}
.news-go{position:absolute;left:25px;top:315px;width:40px;height:40px;border-radius:50%;background:var(--navy);display:flex;align-items:center;justify-content:center}

/* contact */
.field{position:absolute;border:1.5px solid #bbb;background:#fff;font-size:13px;color:#777;padding:18px 22px}
.btn-submit{position:absolute;left:521px;top:3962px;width:158px;height:50px}

/* footer */
.footer-dark{position:absolute;left:0;top:0}
.footer-brand{position:absolute;left:110px;top:4250px;font-family:Montserrat,sans-serif;font-weight:800;font-size:48px;color:#fff;letter-spacing:1px;line-height:1}
.contact-row{position:absolute;left:114px;display:flex;align-items:flex-start;gap:16px;color:#fff;font-size:13px;line-height:28px}
.contact-ico{width:28px;height:28px;border-radius:50%;background:#3a414b;display:flex;align-items:center;justify-content:center;flex:none}
.footer-heading{position:absolute;font-family:Roboto,sans-serif;font-weight:700;font-size:20px;color:#fff}
.footer-heading::after{content:"";display:block;width:38px;height:2px;background:var(--orange);margin-top:10px}
.footer-links{position:absolute;list-style:none;color:#fff;font-size:13px;line-height:28.5px}
.newsletter-input{position:absolute;left:756px;top:4315px;width:332px;height:36px;border-bottom:1.5px solid #7c838c;color:#fff;font-size:13px;padding:4px 8px}
.btn-join{position:absolute;left:761px;top:4372px;width:129px;height:43px;border-radius:22px;background:#e8202a;color:#fff;font-weight:700;font-size:13px;display:flex;align-items:center;justify-content:center}
.social{position:absolute;top:4430px;width:27px;height:27px;border-radius:50%;background:var(--social)}
.copyright{position:absolute;left:0;width:1200px;top:4528px;text-align:center;color:#fff;font-size:13px}
</style>
</head>
<body>

<header class="site-header">
  <div class="brand">VELORA</div>
  <nav class="main-nav">
    <span class="active">HOME</span><span>ABOUT US</span><span>OUR SOFTWARE</span><span>BLOG</span><span>REVIEWS</span><span>CONTACT US</span>
  </nav>
  <div class="btn-login">
    <svg width="11" height="12" viewBox="0 0 11 12"><circle cx="5.5" cy="3" r="3" fill="#fff"/><path d="M0 12c0-4 2.5-5.5 5.5-5.5S11 8 11 12z" fill="#fff"/></svg>LOGIN
  </div>
</header>

<section class="hero">
  <div class="hero-photo" role="img" aria-label="Photo of a young team working at computers in a bright office"></div>
  <div class="hero-shade"></div>
  <h1 class="hero-title">VELORA</h1>
  <p class="hero-sub">WE ARE DEVELOPING SEVERAL PRODUCTS</p>
  <div class="hero-cta btn-orange">GET STARTED
    <svg width="13" height="13" viewBox="0 0 14 14"><circle cx="7" cy="7" r="7" fill="#fff"/><path d="M5 4l3 3-3 3" stroke="#ee6a25" stroke-width="2" fill="none"/></svg>
  </div>
  <div class="hero-arrow" style="left:68px"><svg width="10" height="12"><path d="M7 2L3 6l4 4" stroke="#fff" stroke-width="1.5" fill="none"/></svg></div>
  <div class="hero-arrow" style="left:1084px"><svg width="10" height="12"><path d="M3 2l4 4-4 4" stroke="#fff" stroke-width="1.5" fill="none"/></svg></div>
  <svg class="hero-edge" width="1200" height="782" viewBox="0 0 1200 782">
    <polygon points="0,716 1200,600 1200,782 0,782" fill="#fff"/>
    <polygon points="255,700 1200,600 1200,630 255,716" fill="#d9d9d9"/>
    <polygon points="720,678 1200,618 1200,782" fill="#ee6a25"/>
    <circle cx="600" cy="663" r="60" fill="#fff" stroke="#e2e2e2" stroke-width="2"/>
    <circle cx="600" cy="663" r="40" fill="#1f2630"/>
    <path d="M588 652l12 10 12-10M588 664l12 10 12-10" stroke="#fff" stroke-width="3.5" fill="none"/>
  </svg>
</section>

<!-- about -->
<div class="eyebrow" style="left:110px;top:908px">ABOUT US</div>
<h2 class="section-title" style="left:110px;top:935px">WHO WE ARE</h2>
<div class="about-copy">
  <p>Lorem ipsum dolor sit amet, consectetur adipiscing elit, sed do eiusmod tempor incididunt ut labore et dolore magna aliqua. Ut enim ad minim veniam, quis nostrud exercitation ullamco laboris nisi ut aliquip ex ea commodo consequat. Duis aute irure dolor in reprehenderit in voluptate velit esse cillum dolore eu fugiat nulla pariatur.</p>
  <p>Excepteur sint occaecat cupidatat non proident, sunt in culpa qui officia deserunt mollit anim id est laborum.Lorem ipsum dolor sit amet, consectetur adipiscing elit, sed do eiusmod tempor incididunt ut labore et dolore magna aliqua.</p>
</div>
<div class="btn-learn btn-orange">LEARN MORE
  <svg width="13" height="13" viewBox="0 0 14 14"><circle cx="7" cy="7" r="7" fill="#fff"/><path d="M5 4l3 3-3 3" stroke="#ee6a25" stroke-width="2" fill="none"/></svg>
</div>
<div class="photo" style="left:763px;top:913px;width:294px;height:315px;background:linear-gradient(160deg,#a7b0b8,#56606a)" role="img" aria-label="Photo of team members smiling at a desk"></div>
<div class="about-frame"></div>
<div class="photo" style="left:647px;top:1004px;width:294px;height:315px;background:linear-gradient(150deg,#c9b7a6,#8b6d55 55%,#4e555d)" role="img" aria-label="Photo of two colleagues discussing work at a laptop"></div>

<!-- software -->
<svg class="abs" style="left:0;top:1376px" width="1200" height="890" viewBox="0 0 1200 890">
  <polygon points="0,0 480,100 0,152" fill="#ee6a25"/>
  <polygon points="0,152 1200,62 1200,82 0,172" fill="#d9d9d9"/>
  <polygon points="0,184 1200,63 1200,773 0,888" fill="#1f2630"/>
</svg>
<h2 class="software-title">OUR <span>SOFTWARE</span></h2>
<svg class="abs" style="left:0;top:1650px" width="1200" height="110" viewBox="0 0 1200 110">
  <g stroke="#fff" stroke-width="1.5" stroke-dasharray="4 3" fill="none">
    <path d="M558 2v50H273v50"/><path d="M601 2v100"/><path d="M640 2v50h285v50"/>
  </g>
  <circle cx="273" cy="102" r="8" fill="#ee6a25" stroke="#fff" stroke-width="2"/>
  <circle cx="601" cy="102" r="8" fill="#ee6a25" stroke="#fff" stroke-width="2"/>
  <circle cx="925" cy="102" r="8" fill="#ee6a25" stroke="#fff" stroke-width="2"/>
</svg>

<div class="hex-card" style="left:127px;top:1774px">
  <svg class="hex-shape" width="294" height="322"><polygon points="147,2 292,82 292,240 147,320 2,240 2,82" fill="#fff" stroke="#ee6a25" stroke-width="3"/></svg>
  <div class="hex-icon"><svg width="60" height="60" viewBox="0 0 60 60" fill="none" stroke="#ee6a25" stroke-width="2.5"><path d="M30 28s-10-7-10-13a5 5 0 0 1 10-1 5 5 0 0 1 10 1c0 6-10 13-10 13z"/><path d="M8 44l10-8h12a3 3 0 0 1 0 6h-8M30 42l14-6a3 3 0 0 1 3 5L32 52H8"/></svg></div>
  <div class="hex-label">HEALTHCARE<br>ORGANIZATIONS</div>
</div>
<div class="hex-card" style="left:454px;top:1774px">
  <svg class="hex-shape" width="294" height="322"><polygon points="147,2 292,82 292,240 147,320 2,240 2,82" fill="#fff" stroke="#ee6a25" stroke-width="3"/></svg>
  <div class="hex-icon"><svg width="60" height="60" viewBox="0 0 60 60" fill="none" stroke="#ee6a25" stroke-width="2.5"><path d="M30 8l18 6v14c0 12-9 18-18 22-9-4-18-10-18-22V14z"/><path d="M14 40h32l-4 8H18z"/><circle cx="30" cy="26" r="8"/></svg></div>
  <div class="hex-label">SPORT CLUBS</div>
</div>
<div class="hex-card" style="left:778px;top:1774px">
  <svg class="hex-shape" width="294" height="322"><polygon points="147,2 292,82 292,240 147,320 2,240 2,82" fill="#fff" stroke="#ee6a25" stroke-width="3"/></svg>
  <div class="hex-icon"><svg width="60" height="60" viewBox="0 0 60 60" fill="none" stroke="#ee6a25" stroke-width="2.5"><circle cx="26" cy="14" r="5"/><path d="M26 19v16l-6 14M26 35l6 14M18 26h16M40 30v22M36 40h12v12"/><path d="M14 8l10 22"/></svg></div>
  <div class="hex-label">SPORTS HUNTING</div>
</div>

<!-- testimonials -->
<h2 class="center-title" style="top:2334px"><span class="light">CUSTOMER</span> <b>APPRECIATION</b></h2>
<p class="subtitle" style="top:2398px">See What they are saying About us</p>
<div class="avatar" style="left:336px;top:2493px;width:60px;height:60px;opacity:.7" role="img" aria-label="Customer portrait"></div>
<div class="avatar" style="left:417px;top:2482px;width:82px;height:82px" role="img" aria-label="Customer portrait"></div>
<div class="avatar" style="left:521px;top:2443px;width:160px;height:160px;background:#fff;border:2px solid #ee6a25"></div>
<div class="avatar" style="left:536px;top:2458px;width:130px;height:130px;background:linear-gradient(160deg,#c9ccd0,#6e6258)" role="img" aria-label="Featured customer portrait"></div>
<div class="avatar" style="left:695px;top:2482px;width:82px;height:82px" role="img" aria-label="Customer portrait"></div>
<div class="avatar" style="left:801px;top:2493px;width:60px;height:60px;opacity:.7" role="img" aria-label="Customer portrait"></div>
<div class="dot-deco" style="left:958px;top:2554px;width:24px;height:24px"></div>
<div class="dot-deco" style="left:225px;top:2745px;width:24px;height:24px"></div>
<p class="quote">"Lorem ipsum dolor sit amet, consectetur adipiscing elit, sed do eiusmod tempor incididunt ut labore et dolore magna aliqua. Ut enim ad minim veniam, quis nostrud exercitation ullamco laboris nisi ut aliquip ex ea commodo consequat. Duis aute irure dolor in reprehenderit in voluptate velit esse cillum dolore eu fugiat nulla pariatur. Excepteur sint occaecat cupidatat non proident, sunt in culpa qui officia deserunt mollit anim id est laborum."</p>
<p class="quote-author">- John Doe</p>
<div class="dots"><i></i><i class="on"></i><i></i><i></i><i></i></div>

<!-- news -->
<section class="news">
  <div class="news-photo" role="img" aria-label="Photo of a smiling developer with glasses at a desk with monitors"></div>
  <h2 class="news-title"><span class="light">LATEST</span> <b>NEWS</b></h2>
  <svg class="news-arrow" style="left:696px" width="16" height="22"><path d="M12 3L4 11l8 8" stroke="#fff" stroke-width="2.5" fill="none"/></svg>
  <svg class="news-arrow" style="left:738px" width="16" height="22"><path d="M4 3l8 8-8 8" stroke="#fff" stroke-width="2.5" fill="none"/></svg>
  <article class="news-card" style="left:110px">
    <div class="news-img" role="img" aria-label="Photo of two colleagues laughing at a computer"></div>
    <div class="news-date"><svg width="12" height="12"><rect x="1" y="2" width="10" height="9" fill="none" stroke="#ee6a25" stroke-width="1.5"/><path d="M1 5h10" stroke="#ee6a25"/></svg>Jan 23,2022</div>
    <h3 class="news-head">Lorem ipsum dolor sit amet, consectetur adipiscing</h3>
    <div class="news-go"><svg width="14" height="14"><path d="M2 7h9M7 3l4 4-4 4" stroke="#ee6a25" stroke-width="2.2" fill="none"/></svg></div>
  </article>
  <article class="news-card" style="left:442px">
    <div class="news-img" role="img" aria-label="Photo of a team working at several screens"></div>
    <div class="news-date"><svg width="12" height="12"><rect x="1" y="2" width="10" height="9" fill="none" stroke="#ee6a25" stroke-width="1.5"/><path d="M1 5h10" stroke="#ee6a25"/></svg>Jan 23,2022</div>
    <h3 class="news-head">Lorem ipsum dolor sit amet, consectetur adipiscing</h3>
    <div class="news-go"><svg width="14" height="14"><path d="M2 7h9M7 3l4 4-4 4" stroke="#ee6a25" stroke-width="2.2" fill="none"/></svg></div>
  </article>
</section>

<!-- contact -->
<h2 class="center-title" style="top:3580px"><span class="light">GET</span> <b class="accent">IN TOUCH</b></h2>
<div class="field" style="left:239px;top:3653px;width:351px;height:57px">First name</div>
<div class="field" style="left:608px;top:3653px;width:351px;height:57px">Last name</div>
<div class="field" style="left:239px;top:3728px;width:351px;height:57px">Phone</div>
<div class="field" style="left:608px;top:3728px;width:351px;height:57px">Email address</div>
<div class="field" style="left:239px;top:3805px;width:720px;height:135px">Message</div>
<div class="btn-submit btn-orange">SUBMIT</div>

<!-- footer -->
<svg class="footer-dark" style="top:4020px" width="1200" height="574" viewBox="0 0 1200 574">
  <polygon points="720,90 1200,8 1200,160" fill="#ee6a25"/>
  <polygon points="0,60 1200,150 1200,574 0,574" fill="#1f2630"/>
  <polygon points="0,60 720,114 1200,90 1200,150" fill="#252c36"/>
</svg>
<div class="footer-brand">VELORA</div>
<div class="contact-row" style="top:4324px">
  <span class="contact-ico"><svg width="10" height="13"><path d="M5 13S0 7 0 5a5 5 0 0 1 10 0c0 2-5 8-5 8z" fill="#fff"/><circle cx="5" cy="5" r="2" fill="#3a414b"/></svg></span>
  <span>Lorem ipsum dolor sit amet,<br>consectetur</span>
</div>
<div class="contact-row" style="top:4380px">
  <span class="contact-ico"><svg width="12" height="12"><path d="M2 1l3 0 1 3-2 1a7 7 0 0 0 3 3l1-2 3 1v3c-6 1-10-4-9-9z" fill="#fff"/></svg></span>
  <span>+1 888 888 8888</span>
</div>
<div class="contact-row" style="top:4438px">
  <span class="contact-ico"><svg width="12" height="10"><rect x="0" y="0" width="12" height="10" fill="#fff"/><path d="M0 0l6 5 6-5" stroke="#3a414b" fill="none"/></svg></span>
  <span>info@companyname.com</span>
</div>
<div class="footer-heading" style="left:417px;top:4262px">Information</div>
<ul class="footer-links" style="left:417px;top:4316px"><li>Home</li><li>Our Software</li><li>Team</li><li>Our story</li><li>Industry</li></ul>
<ul class="footer-links" style="left:615px;top:4316px"><li>Locations</li><li>Faq</li><li>Latest news</li><li>Faq</li><li>Contact us</li></ul>
<div class="footer-heading" style="left:756px;top:4262px">Join our Newsletter</div>
<div class="newsletter-input">Enter your name*</div>
<div class="btn-join">JOIN NOW!</div>
<span class="social" style="left:762px"></span>
<span class="social" style="left:796px"></span>
<span class="social" style="left:831px"></span>
<p class="copyright">© Copyrights 2022 All Rights Reserved &nbsp;|&nbsp; Terms &nbsp;|&nbsp; Privacy &nbsp;|&nbsp; Disclaimer</p>

</body>
</html>
```